Logo + Label Design (Men’s Grooming Brand & Product Packaging)

Design a logo and 2 oz pomade label for Brel, a modern men’s grooming brand focused on clean, high-quality, natural ingredients. The design should establish a bold, masculine, minimalist identity that can later extend to products like shaving gel and body wash.

Key Requirements

Create a primary logo for “Brel” and a core label for the 2 oz pomade jar (screw-top).

Use a clean, modern style — masculine, confident, and approachable (think Dorran’s, Velta, Northfield Kit).

Design for 1–2 color screen printing on solid jar colors (white, black, or navy).

Avoid gradients, foil, or embossing. Must work in black & white.

Provide: vector logo, mockup of the 2 oz jar, color palette (CMYK/RGB/HEX), and font specs.

Winning design may lead to future projects (body wash, shave gel, skincare lines).

Font styles to use
Other font styles liked:
• We like the fonts and design concept in the attached mockup.

Requirements
Should not have
• We want to avoid too much writing or busy designs. We want to avoid having graphics/illustrations embedded in the logo if they will cause the brand to look less classy or sophisticated. We also want the design to look simple and all-American (e.g. Hollister and Vane, Pine Ledger, The KIM, etc). We’d like to give a Pellham & Royce vibe that feels classy and high end.

```html
<!DOCTYPE html>
<html lang="en">
<head>
<meta charset="UTF-8">
<title>Brel Hair Pomade Label</title>
<link rel="stylesheet" href="https://fonts.googleapis.com/css2?family=Montserrat:wght@400;500;600&display=swap">
<style>
  :root {
    --backdrop: #cfcdcd;
    --label-white: #ffffff;
    --lid-white: #e1e4e8;
    --gold: #d8b62c;
    --navy: #0b3d7e;
    --ink: #0a0a0a;
    --argan-dark: #8a5a32;
    --argan-light: #d9b78a;
  }
  * { box-sizing: border-box; margin: 0; padding: 0; }
  html, body { width: 1200px; height: 800px; overflow: hidden; background: var(--backdrop); }
  .canvas { position: relative; width: 1200px; height: 800px; background: var(--backdrop); font-family: "Montserrat", Arial, sans-serif; }

  /* Side wrap label */
  .side-label {
    position: absolute; left: 162px; top: 420px; width: 392px; height: 176px;
    background: var(--label-white);
    border-top: 6px solid var(--gold); border-bottom: 6px solid var(--gold);
  }
  .side-label .wordmark { position: absolute; left: 0; right: 0; top: 14px; text-align: center; font-size: 60px; }
  .side-label .product-name { position: absolute; left: 0; right: 0; top: 88px; text-align: center; font-size: 15px; }
  .side-label .argan-art { position: absolute; left: 292px; top: 76px; width: 46px; height: 34px; }
  .side-label .specs { position: absolute; left: 0; right: 0; top: 128px; font-size: 8px; line-height: 12px; }

  /* Lid label */
  .lid-label {
    position: absolute; left: 641px; top: 176px; width: 392px; height: 392px;
    border-radius: 50%; background: var(--lid-white);
  }
  .lid-label .gold-ring { position: absolute; inset: 17px; border-radius: 50%; border: 3px solid var(--gold); }
  .lid-label .argan-art { position: absolute; left: 148px; top: 70px; width: 96px; height: 64px; }
  .lid-label .wordmark { position: absolute; left: 0; right: 0; top: 148px; text-align: center; font-size: 96px; }
  .lid-label .product-name { position: absolute; left: 0; right: 0; top: 268px; text-align: center; font-size: 22px; }
  .lid-label .hold { position: absolute; left: 0; right: 0; top: 330px; font-size: 10px; }
  .lid-label .weight { position: absolute; left: 0; right: 0; top: 352px; font-size: 10px; }

  /* Shared type */
  .wordmark { font-weight: 600; color: var(--ink); line-height: 1; letter-spacing: 2px; }
  .product-name { font-weight: 500; color: var(--navy); letter-spacing: 1px; line-height: 1.2; }
  .specs, .hold, .weight { font-weight: 400; color: var(--ink); text-align: center; }
  .argan-art { border-radius: 50%; background: radial-gradient(circle at 45% 55%, var(--argan-light) 0 25%, var(--argan-dark) 60%); }
</style>
</head>
<body>
<main class="canvas">
  <section class="side-label" aria-label="Jar side wrap label">
    <h2 class="wordmark">Brel</h2>
    <p class="product-name">Hair Pomade</p>
    <div class="argan-art" role="img" aria-label="Illustration of split argan nuts with a leaf and a drop of oil"></div>
    <p class="specs">Medium Hold - Matte Finish<br>Net WT 2 oz (57g)</p>
  </section>

  <section class="lid-label" aria-label="Jar lid label">
    <div class="gold-ring"></div>
    <div class="argan-art" role="img" aria-label="Illustration of split argan nuts with a leaf and a drop of oil"></div>
    <h1 class="wordmark">Brel</h1>
    <p class="product-name">Hair Pomade</p>
    <p class="hold">Medium Hold - Matte Finish</p>
    <p class="weight">Net WT 2 oz (57g)</p>
  </section>
</main>
</body>
</html>
```